PERI VALORE

We need a letterhead design for an Image & Etiquette Consultancy company based in Singapore.

The services we provide are Personal Image Consultation, Image & Etiquette Workshop for schools and corporate.

The design should have our corporate colour as seen in the logo files I have uploaded.

Since our company helps clients with their image, the design should be aesthetically very appealing. It should reflect a very classy & elegant feel.

I will print the letterhead using my printer but most of the time will use it to write letters to my clients therefore the format should include MS Word.

```html
<!DOCTYPE html>
<html lang="en">
<head>
<meta charset="utf-8">
<title>Peri Valore Letterhead</title>
<link rel="stylesheet" href="https://fonts.googleapis.com/css2?family=Questrial&family=Open+Sans:wght@600;700&display=swap">
<style>
  :root {
    --paper: #ffffff;
    --plum: #3b1c4f;
    --ink: #2c2a30;
    --faint: #e7e5ea;
    --gold-deep: #c3922c;
    --gold-mid: #e9c23f;
    --gold-light: #fff4c6;
  }
  html, body {
    margin: 0;
    padding: 0;
    width: 971px;
    height: 1200px;
    overflow: hidden;
    background: var(--paper);
  }
  .letterhead {
    position: relative;
    width: 971px;
    height: 1200px;
    background: var(--paper);
  }
  .brand-name {
    position: absolute;
    top: 86px;
    left: 0;
    width: 100%;
    margin: 0;
    text-align: center;
    font-family: "Questrial", sans-serif;
    font-weight: 400;
    font-size: 60px;
    letter-spacing: 1px;
    line-height: 1;
    color: var(--plum);
  }
  .brand-watermark {
    position: absolute;
    top: 798px;
    left: 0;
    width: 100%;
    text-align: center;
    font-family: "Questrial", sans-serif;
    font-weight: 400;
    font-size: 60px;
    letter-spacing: 1px;
    line-height: 1;
    color: var(--faint);
  }
  .gold-rule {
    position: absolute;
    left: 0;
    top: 1147px;
    width: 658px;
    height: 19px;
    background: linear-gradient(90deg,
      var(--gold-deep) 0%,
      #d3a934 25%,
      var(--gold-mid) 55%,
      var(--gold-light) 66%,
      var(--gold-mid) 76%,
      var(--gold-deep) 100%);
  }
  .contact-list {
    position: absolute;
    left: 683px;
    top: 1098px;
    margin: 0;
    padding: 0;
    list-style: none;
    font-family: "Open Sans", sans-serif;
    color: var(--ink);
  }
  .contact-item {
    display: flex;
    align-items: center;
    gap: 10px;
  }
  .contact-item svg { fill: var(--plum); flex: none; }
  .contact-phone {
    font-size: 19px;
    font-weight: 700;
    letter-spacing: 0.5px;
    margin-bottom: 10px;
  }
  .contact-small {
    font-size: 14px;
    font-weight: 600;
    letter-spacing: 0.4px;
    margin-bottom: 3px;
  }
</style>
</head>
<body>
  <main class="letterhead">
    <h1 class="brand-name">PERI VALORE</h1>

    <div class="brand-watermark" aria-hidden="true">PERI VALORE</div>

    <div class="gold-rule"></div>

    <ul class="contact-list">
      <li class="contact-item contact-phone">
        <svg width="14" height="24" viewBox="0 0 14 24" aria-hidden="true">
          <rect x="1" y="3" width="12" height="20" rx="2"/>
          <rect x="9" y="0" width="2" height="4"/>
          <rect x="3.5" y="6" width="7" height="5" fill="#ffffff"/>
        </svg>
        <span>06543219870</span>
      </li>
      <li class="contact-item contact-small">
        <svg width="14" height="12" viewBox="0 0 14 12" aria-hidden="true">
          <rect x="0" y="1" width="14" height="10" rx="1.5"/>
          <path d="M1 2 L7 7 L13 2" stroke="#ffffff" stroke-width="1.4" fill="none"/>
        </svg>
        <span>hello@perivalore.com</span>
      </li>
      <li class="contact-item contact-small">
        <svg width="14" height="14" viewBox="0 0 14 14" aria-hidden="true">
          <circle cx="7" cy="7" r="6.5"/>
          <path d="M0.5 7 H13.5 M7 0.5 V13.5 M2 3.5 H12 M2 10.5 H12" stroke="#ffffff" stroke-width="1" fill="none"/>
          <ellipse cx="7" cy="7" rx="3" ry="6.5" stroke="#ffffff" stroke-width="1" fill="none"/>
        </svg>
        <span>perivalore-image.com</span>
      </li>
    </ul>
  </main>
</body>
</html>
```